Business Card Design for Occupational Medicine Start Up Company

We need to design a professional business card. We are a healthcare company providing occupational medicine services to blue collar industries. We are professional, efficient and high quality service providers.

Target Market(s)

Blue Collar Industry: Shipbuilding, Ports, Trucking Companies; The Executives and Safety Officers for these companies

Industry/Entity Type

Healthcare

Contact Information for Business Card

Logo, Name, Title, Email, Phone

Other font styles liked:
• Please match our Brand Guide

Requirements
Must have
• Our Company Colors and Logo

```html
<!DOCTYPE html>
<html lang="en">
<head>
<meta charset="utf-8">
<title>Harborline Clinics – Business Card</title>
<link rel="stylesheet" href="https://fonts.googleapis.com/css2?family=Montserrat:wght@700&family=Didact+Gothic&display=swap">
<style>
  :root {
    --page-bg: #2a2a2c;
    --card-bg: #1d1e20;
    --pattern-bg: #19191b;
    --ink: #ffffff;
    --ink-soft: #c9c9cc;
    --divider: #5a5b5e;
  }
  * { margin: 0; padding: 0; box-sizing: border-box; }
  html, body {
    width: 1200px; height: 1024px; overflow: hidden;
    background: var(--page-bg);
  }
  .card {
    position: absolute; left: 220px;
    width: 760px; height: 434px;
    background: var(--card-bg);
    box-shadow: 0 10px 30px rgba(0,0,0,.5);
    overflow: hidden;
  }
  .card--front { top: 50px; }
  .card--back { top: 530px; }

  .brand {
    position: absolute;
    display: flex; align-items: center; gap: 14px;
    font-family: "Montserrat", sans-serif; font-weight: 700;
    color: var(--ink); text-transform: uppercase;
    line-height: 1.1;
  }
  .brand__dot {
    width: 22px; height: 22px; border-radius: 50%;
    background: var(--ink); flex: none;
  }
  .card--front .brand { left: 70px; top: 180px; font-size: 26px; letter-spacing: 1px; }
  .card--back .brand { right: 64px; bottom: 74px; font-size: 20px; letter-spacing: 1px; }

  .divider {
    position: absolute; left: 400px; top: 110px;
    width: 1px; height: 214px; background: var(--divider);
  }
  .contact {
    position: absolute; left: 440px; top: 118px;
    font-family: "Didact Gothic", sans-serif; color: var(--ink-soft);
  }
  .contact__name {
    font-family: "Montserrat", sans-serif; font-weight: 700;
    font-size: 30px; color: var(--ink); letter-spacing: 1px;
  }
  .contact__title { font-size: 16px; margin-top: 2px; margin-bottom: 22px; }
  .contact__list { list-style: none; }
  .contact__item {
    display: flex; align-items: center; gap: 10px;
    font-size: 19px; margin-bottom: 10px;
  }
  .contact__icon {
    width: 18px; height: 18px; border-radius: 50%;
    background: var(--ink); flex: none;
    display: flex; align-items: center; justify-content: center;
  }
  .contact__icon svg { width: 11px; height: 11px; fill: var(--card-bg); }

  .pattern-area {
    position: absolute; inset: 0;
    background: linear-gradient(135deg, #1c1c1e, var(--pattern-bg));
  }
</style>
</head>
<body>
  <section class="card card--front">
    <div class="brand">
      <span class="brand__dot"></span>
      <span>Harborline<br>Clinics</span>
    </div>
    <div class="divider"></div>
    <div class="contact">
      <h1 class="contact__name">DANA REYES</h1>
      <p class="contact__title">Executive Manage</p>
      <ul class="contact__list">
        <li class="contact__item">
          <span class="contact__icon"><svg viewBox="0 0 24 24"><path d="M6.6 10.8a15 15 0 0 0 6.6 6.6l2.2-2.2a1 1 0 0 1 1-.25 11.4 11.4 0 0 0 3.6.57 1 1 0 0 1 1 1V20a1 1 0 0 1-1 1A17 17 0 0 1 3 4a1 1 0 0 1 1-1h3.5a1 1 0 0 1 1 1c0 1.25.2 2.45.57 3.57a1 1 0 0 1-.25 1z"/></svg></span>
          555-014-2290
        </li>
        <li class="contact__item">
          <span class="contact__icon"><svg viewBox="0 0 24 24"><path d="M2 5h20v14H2zm2 2v.5l8 5 8-5V7l-8 5z"/></svg></span>
          info@harborlineclinics.com
        </li>
        <li class="contact__item">
          <span class="contact__icon"><svg viewBox="0 0 24 24"><path d="M12 3 2 12h3v8h5v-5h4v5h5v-8h3z"/></svg></span>
          Your address, your city, box 88900
        </li>
      </ul>
    </div>
  </section>

  <section class="card card--back">
    <div class="pattern-area" role="img" aria-label="Tone-on-tone embossed brand pattern covering the card back"></div>
    <div class="brand">
      <span>Harborline<br>Clinics</span>
    </div>
  </section>
</body>
</html>
```